Tolvar Air and Electrical Website

Simple and easy to use website for a Electrical and Air Conditioning contracting business.Use stock photosOnline contact portallogo still to be supplied

Target Market(s)

Mums and Dads who want a local contractor

Coding

Coded - Design and coding required

Number of Pages Required

2 page

Font styles to use
Sans Serif

Colors
f04a50
3276b5
33a6d7

Requirements
Must have
• Simple and easy to use
• Ph number
• 4 web address; linked to page
• 0417385926
• tolvar.com.au
• tolvarelectrical.com.au
• tolvarairandelectrical.com.au
• tolvarair.com.au
Nice to have
• Split System Air Con Picture
• Electrical Pictures

```html
<!DOCTYPE html>
<html lang="en">
<head>
<meta charset="utf-8">
<title>Tolvar Air and Electrical</title>
<link href="https://fonts.googleapis.com/css2?family=Montserrat:wght@400;500;600;700;800&family=Quicksand:wght@400;500;600&family=Oswald:wght@400&display=swap" rel="stylesheet">
<style>
:root{
  --blue:#1a72c0;
  --blue-dark:#125fa8;
  --blue-light:#33a6d7;
  --red:#ee1c25;
  --ink:#333333;
  --muted:#666666;
  --field:#f2f2f2;
  --white:#ffffff;
}
*{box-sizing:border-box;margin:0;padding:0}
html,body{width:1200px;height:4380px;overflow:hidden;background:var(--white)}
body{font-family:'Quicksand',sans-serif;color:var(--ink)}
.canvas{position:relative;width:1200px;height:4380px;overflow:hidden}
.abs{position:absolute}
.heading{font-family:'Montserrat',sans-serif;font-weight:600;text-transform:uppercase}
.btn{position:absolute;background:var(--red);color:var(--white);font-family:'Montserrat',sans-serif;font-weight:600;text-transform:uppercase;display:flex;align-items:center;justify-content:center}

/* header */
.topbar-phone{left:775px;top:10px;font-size:15px;color:var(--white);display:flex;align-items:center;gap:8px;z-index:3}
.topbar-bg{left:0;top:0;width:1200px;height:42px;background:var(--blue)}
.quote-btn{left:925px;top:0;width:197px;height:50px;font-size:16px;border-radius:0 0 4px 4px;z-index:3}
.header{left:0;top:42px;width:1200px;height:82px;background:var(--white)}
.brand{left:76px;top:58px;display:flex;align-items:center;gap:10px}
.brand-mark{width:46px;height:46px;background:var(--blue)}
.brand-name{font-family:'Montserrat',sans-serif;font-weight:700;color:var(--blue);font-size:26px;line-height:1;letter-spacing:.5px}
.brand-sub{font-family:'Montserrat',sans-serif;font-weight:700;color:var(--blue);font-size:11px;letter-spacing:2.5px;margin-top:3px}
.nav{left:578px;top:79px;display:flex;gap:0;font-family:'Montserrat',sans-serif;font-size:14px;color:#444}
.nav a{color:inherit;text-decoration:none;position:absolute;white-space:nowrap}
.nav .active{color:var(--red)}
.nav .active::before{content:"";position:absolute;left:-16px;top:6px;width:7px;height:7px;border-radius:50%;background:var(--red)}

/* hero */
.hero{left:0;top:124px;width:1200px;height:553px;background:linear-gradient(100deg,#e9edf1 0%,#d9dee3 45%,#c5ccd3 70%,#aab2ba 100%)}
.hero-title{left:80px;top:292px;font-family:'Montserrat',sans-serif;font-weight:800;font-size:54px;line-height:56px;color:var(--blue);text-transform:uppercase}
.hero-sub{left:80px;top:412px;font-family:'Oswald',sans-serif;font-size:21px;color:#222}
.hero-btn{left:77px;top:457px;width:181px;height:51px;font-size:20px}
.hero-dots{left:1157px;top:312px;display:flex;flex-direction:column;gap:14px}
.hero-dots span{width:13px;height:13px;border-radius:50%;background:var(--blue-light)}
.hero-dots .on{background:var(--red);width:15px;height:15px;margin-left:-1px}

/* welcome */
.welcome-title{left:0;top:735px;width:1200px;text-align:center;font-size:44px;color:var(--white);font-weight:500}
.welcome-text{left:270px;top:804px;width:660px;text-align:center;color:var(--white);font-size:13.5px;line-height:27px}
.welcome-text p+p{margin-top:14px}
.chev{left:574px;top:977px;width:52px;height:52px;border-radius:50%;background:var(--red)}

/* services */
.sec-title{left:0;width:1200px;text-align:center;color:var(--blue);font-size:41px;font-weight:500}
.sec-kicker{left:0;width:1200px;text-align:center;color:var(--red);font-family:'Montserrat',sans-serif;font-weight:600;font-size:14px}
.svc-label{font-family:'Montserrat',sans-serif;font-weight:500;font-size:14px;color:#222;text-transform:uppercase;line-height:23px}

/* why */
.why-title{left:551px;top:2093px;font-size:42px;color:var(--white);font-weight:500}
.why-text{left:553px;top:2162px;width:520px;font-size:15px;font-style:italic;line-height:29px;color:var(--white)}
.why-btn{left:553px;top:2270px;width:192px;height:50px;font-size:20px}

/* contact */
.contact-title{left:0;top:2560px;width:1200px;text-align:center;font-size:40px;line-height:44px;color:var(--blue);font-weight:500}
.contact-sub{left:0;top:2657px;width:1200px;text-align:center;font-size:16px;color:#666}
.field{left:330px;width:540px;background:var(--field);font-size:13px;color:#777;padding:0 17px;display:flex;align-items:center}
.field.focus{background:var(--white);border:1.5px solid var(--blue)}
.field.area{align-items:flex-start;padding-top:15px}
.submit{left:529px;top:2985px;width:144px;height:50px;font-size:20px}

/* feedback */
.fb-title{left:0;top:3180px;width:1200px;text-align:center;font-size:42px;color:var(--white);font-weight:500}
.fb-photo{left:0;top:3264px;width:1200px;height:447px;background:linear-gradient(180deg,#4a4d52 0%,#3a3c40 50%,#2c2e31 100%)}
.fb-box{left:235px;top:3318px;width:731px;height:286px;background:rgba(30,30,32,.72)}
.fb-quote{left:566px;top:3324px;width:68px;height:68px;border-radius:50%;background:var(--red);color:var(--white);font-family:'Montserrat',sans-serif;font-weight:800;font-size:44px;display:flex;align-items:center;justify-content:center}
.fb-text{left:280px;top:3420px;width:640px;text-align:center;color:var(--white);font-size:13.5px;line-height:27px}
.fb-name{left:0;top:3530px;width:1200px;text-align:center;color:var(--blue-light);font-family:'Montserrat',sans-serif;font-size:17px;text-transform:uppercase}
.fb-date{left:0;top:3560px;width:1200px;text-align:center;color:var(--red);font-size:13px}
.fb-btn{left:479px;top:3689px;width:243px;height:49px;font-size:20px;z-index:2}

/* call */
.call{left:0;top:3711px;width:1200px;height:267px;background:var(--blue)}
.call-label{left:301px;top:3803px;font-size:36px;color:var(--white);font-weight:500}
.call-icon{left:566px;top:3793px;width:68px;height:68px;border-radius:50%;background:var(--white);display:flex;align-items:center;justify-content:center}
.call-icon span{width:54px;height:54px;border-radius:50%;background:var(--red);display:flex;align-items:center;justify-content:center}
.call-number{left:668px;top:3800px;font-family:'Montserrat',sans-serif;font-weight:500;font-size:38px;color:var(--white)}
.call-text{left:280px;top:3872px;width:640px;text-align:center;color:var(--white);font-size:15px;line-height:27px}

/* footer */
.foot-head{top:4016px;font-family:'Montserrat',sans-serif;font-weight:600;font-size:15px;color:var(--blue);text-transform:uppercase}
.foot-list{top:4062px;list-style:none;font-size:13px;color:#555}
.foot-list li{height:29px;position:relative;padding-left:16px}
.foot-list li::before{content:"";position:absolute;left:0;top:6px;width:6px;height:6px;border-radius:50%;background:var(--red)}
.foot-contact{left:876px;top:4062px;list-style:none;font-size:13px;color:#555}
.foot-contact li{position:absolute;left:0;display:flex;align-items:center;gap:18px;white-space:nowrap}
.foot-contact svg{flex:none}
.social{top:4167px;display:flex;gap:9px;left:106px}
.social span{width:40px;height:40px;border-radius:50%;border:1.5px solid var(--blue)}
.foot-rule{left:76px;top:4313px;width:1048px;height:1px;background:#dddddd}
.copy{left:0;top:4338px;width:1200px;text-align:center;font-size:13px;color:#555}
</style>
</head>
<body>
<div class="canvas">

  <!-- header -->
  <div class="abs topbar-bg"></div>
  <div class="abs topbar-phone">
    <svg width="22" height="22" viewBox="0 0 22 22"><circle cx="11" cy="11" r="10" fill="none" stroke="#fff" stroke-width="1.5"/><path d="M7.5 6.5c1-.8 1.6-.6 2 .3l.6 1.4c.2.6 0 1-.5 1.4-.4.3-.4.6-.1 1.1.6 1 1.3 1.7 2.2 2.2.5.3.8.3 1.1-.1.4-.5.8-.7 1.4-.5l1.4.6c.9.4 1.1 1 .3 2-1 1.2-2.4 1.3-4.4 0-1.9-1.2-3.3-2.6-4.4-4.5-1-1.9-.8-3.1.4-3.9z" fill="#fff"/></svg>
    041 738 5926
  </div>
  <div class="btn quote-btn">Request a Quote</div>
  <div class="abs header"></div>
  <div class="abs brand">
    <div class="brand-mark"></div>
    <div>
      <div class="brand-name">TOLVAR</div>
      <div class="brand-sub">AIR AND ELECTRICAL</div>
    </div>
  </div>
  <nav class="abs nav">
    <a class="active" style="left:17px">HOME</a>
    <a style="left:97px">ABOUT</a>
    <a style="left:177px">WHY US</a>
    <a style="left:267px">SERVICES</a>
    <a style="left:359px">FEEDBACK</a>
    <a style="left:451px">CONTACT US</a>
  </nav>

  <!-- hero -->
  <div class="abs hero" role="img" aria-label="Photo of a technician in a cap servicing a wall-mounted split system air conditioner"></div>
  <h1 class="abs hero-title">Tolvar Air and<br>Electrical</h1>
  <div class="abs hero-sub">We also respond to your phone calls and emails within 24 hours.</div>
  <div class="btn hero-btn">Contact Us</div>
  <div class="abs hero-dots"><span></span><span></span><span class="on"></span><span></span><span></span></div>

  <!-- welcome -->
  <svg class="abs" style="left:0;top:677px" width="1200" height="465" viewBox="0 0 1200 465">
    <defs>
      <linearGradient id="welcomeGrad" x1="0" y1="0" x2="1" y2="0">
        <stop offset="0" stop-color="#33a6d7"/>
        <stop offset="1" stop-color="#1a6fbd"/>
      </linearGradient>
    </defs>
    <polygon points="0,0 1200,0 1200,272 970,465 365,391 0,465" fill="url(#welcomeGrad)"/>
    <polygon points="970,465 1200,272 1200,345" fill="#ee1c25"/>
  </svg>
  <h2 class="abs heading welcome-title">Welcome to Tolvar</h2>
  <div class="abs welcome-text">
    <p>With over 17 years' experience in the Electrical Industry, Tolvar Electrical provides a superior level of knowledge, a broad range of products and a high standard of customer service.</p>
    <p>To provide our customers with an immediate response within their timeframe, and deliver on-time, every time. Our friendly tradesmen are always professionally attired and treat your home or business with respect - we leave our jobs clean and tidy.</p>
  </div>
  <div class="abs chev">
    <svg width="52" height="52" viewBox="0 0 52 52"><path d="M18 21l8 7 8-7M18 27l8 7 8-7" fill="none" stroke="#fff" stroke-width="2"/></svg>
  </div>

  <!-- services -->
  <h2 class="abs heading sec-title" style="top:1185px">Our Services</h2>
  <div class="abs sec-kicker" style="top:1235px">WHAT WE DO</div>
  <svg class="abs" style="left:0;top:1280px" width="1200" height="620" viewBox="0 1280 1200 620">
    <g fill="none" stroke="#1a72c0" stroke-width="1.3">
      <circle cx="600" cy="1513" r="199"/>
      <polyline points="273,1335 345,1335 440,1397" stroke="#ee1c25"/>
      <polyline points="927,1335 855,1335 760,1397"/>
      <line x1="273" y1="1513" x2="401" y2="1513"/>
      <line x1="927" y1="1513" x2="799" y2="1513"/>
      <polyline points="273,1693 345,1693 440,1630"/>
      <polyline points="927,1693 855,1693 760,1630"/>
      <line x1="600" y1="1712" x2="600" y2="1800"/>
    </g>
    <g fill="#1a72c0">
      <circle cx="440" cy="1397" r="6" fill="#ee1c25"/>
      <circle cx="760" cy="1397" r="4"/>
      <circle cx="401" cy="1513" r="4"/>
      <circle cx="799" cy="1513" r="4"/>
      <circle cx="440" cy="1630" r="4"/>
      <circle cx="760" cy="1630" r="4"/>
      <circle cx="600" cy="1712" r="4"/>
    </g>
    <!-- icon circles -->
    <g>
      <circle cx="223" cy="1335" r="48" fill="#fff" stroke="#ee1c25" stroke-width="2"/>
      <circle cx="223" cy="1335" r="41" fill="#ee1c25"/>
      <circle cx="976" cy="1335" r="48" fill="#fff" stroke="#1a72c0" stroke-width="2"/>
      <circle cx="976" cy="1335" r="41" fill="#1a72c0"/>
      <circle cx="223" cy="1513" r="48" fill="#fff" stroke="#1a72c0" stroke-width="2"/>
      <circle cx="223" cy="1513" r="41" fill="#1a72c0"/>
      <circle cx="976" cy="1513" r="48" fill="#fff" stroke="#1a72c0" stroke-width="2"/>
      <circle cx="976" cy="1513" r="41" fill="#1a72c0"/>
      <circle cx="223" cy="1693" r="48" fill="#fff" stroke="#1a72c0" stroke-width="2"/>
      <circle cx="223" cy="1693" r="41" fill="#1a72c0"/>
      <circle cx="976" cy="1693" r="48" fill="#fff" stroke="#1a72c0" stroke-width="2"/>
      <circle cx="976" cy="1693" r="41" fill="#1a72c0"/>
      <circle cx="600" cy="1850" r="48" fill="#fff" stroke="#1a72c0" stroke-width="2"/>
      <circle cx="600" cy="1850" r="41" fill="#1a72c0"/>
    </g>
    <g fill="none" stroke="#fff" stroke-width="2">
      <!-- domestic: meter -->
      <rect x="207" y="1316" width="24" height="36" rx="2"/><rect x="211" y="1321" width="16" height="9"/><circle cx="219" cy="1340" r="5"/><line x1="236" y1="1318" x2="236" y2="1352"/>
      <!-- commercial: building -->
      <rect x="960" y="1318" width="26" height="34"/><line x1="986" y1="1330" x2="994" y2="1330"/><line x1="994" y1="1330" x2="994" y2="1352"/><path d="M965 1326h5M974 1326h5M965 1334h5M974 1334h5M965 1342h5M974 1342h5"/>
      <!-- split system -->
      <rect x="200" y="1500" width="46" height="18" rx="4"/><path d="M206 1507h34M206 1512h34M208 1524l-2 4M216 1524l-2 4M224 1524l-2 4M232 1524l-2 4"/>
      <!-- testing -->
      <rect x="960" y="1496" width="24" height="32" rx="2"/><circle cx="990" cy="1500" r="7"/><path d="M965 1503h14M965 1510h14M965 1517h10"/>
      <!-- data -->
      <rect x="202" y="1676" width="38" height="9"/><rect x="202" y="1689" width="38" height="9"/><rect x="202" y="1702" width="38" height="9"/><circle cx="240" cy="1692" r="7"/>
      <!-- breakdown: tools -->
      <path d="M960 1712l30-30M966 1678l24 26M988 1680l4-4"/><circle cx="963" cy="1680" r="4"/>
      <!-- industrial: factory -->
      <path d="M580 1870v-18l10-6v6l10-6v6l10-6v24zM590 1846v-14h5v10M612 1870v-26h6v26z"/>
    </g>
    <!-- centre photo -->
    <circle cx="600" cy="1513" r="184" fill="#8c97a0" role="img" aria-label="Photo of a technician kneeling beside an outdoor air conditioning unit with a tool bag"/>
  </svg>
  <div class="abs svc-label" style="left:179px;top:1396px">Domestic</div>
  <div class="abs svc-label" style="left:944px;top:1396px">Commercial</div>
  <div class="abs svc-label" style="left:138px;top:1576px;text-align:center">Split System<br>Installations</div>
  <div class="abs svc-label" style="left:944px;top:1576px">Electrical Testing &amp;<br>Tagging</div>
  <div class="abs svc-label" style="left:78px;top:1755px;text-align:right">Data &amp; Communication<br>Installation</div>
  <div class="abs svc-label" style="left:944px;top:1755px">24hr Breakdown &amp;<br>Repair Service</div>
  <div class="abs svc-label" style="left:553px;top:1914px">Industrial</div>

  <!-- why us -->
  <svg class="abs" style="left:0;top:1940px" width="1200" height="600" viewBox="0 0 1200 600">
    <polygon points="0,75 230,40 0,150" fill="#ee1c25"/>
    <polygon points="0,150 230,40 470,70 1020,4 1200,100 1200,492 493,542 0,457" fill="#1a6fbd"/>
    <polygon points="1020,4 1200,60 1200,100 1150,76" fill="#ee1c25"/>
    <polygon points="493,542 1200,491 1200,596" fill="#ee1c25"/>
  </svg>
  <div class="abs" style="left:119px;top:2015px;width:300px;height:433px;background:linear-gradient(180deg,#2d5fae,#1f4e96)" role="img" aria-label="Photo of a smiling electrician in blue overalls giving thumbs up"></div>
  <div class="abs" style="left:330px;top:2312px;width:165px;height:110px;background:#e6e9ec" role="img" aria-label="Photo of an outdoor air conditioner unit"></div>
  <h2 class="abs heading why-title">Why Us ?</h2>
  <p class="abs why-text">On Time We arrive on time. If there is an unavoidable delay we'll call ahead to let you know when we'll be there. We also respond to your phone calls and emails within 24 hours.</p>
  <div class="btn why-btn">Learn More</div>

  <!-- contact -->
  <h2 class="abs heading contact-title">Contact us today for<br>a quote!</h2>
  <p class="abs contact-sub">If you need an have any question for contact us today !</p>
  <div class="abs field focus" style="top:2708px;height:44px">Name *</div>
  <div class="abs field" style="top:2764px;height:46px">Email *</div>
  <div class="abs field" style="top:2824px;height:46px">Phone *</div>
  <div class="abs field area" style="top:2882px;height:90px">Message *</div>
  <div class="btn submit">Submit</div>

  <!-- feedback -->
  <svg class="abs" style="left:0;top:3000px" width="1200" height="264" viewBox="0 0 1200 264">
    <polygon points="0,120 195,74 0,179" fill="#ee1c25"/>
    <polygon points="0,180 195,74 800,124 1200,40 1200,264 0,264" fill="#1a6fbd"/>
    <polygon points="800,124 1200,9 1200,40" fill="#ee1c25"/>
  </svg>
  <h2 class="abs heading fb-title">Client Feedback</h2>
  <div class="abs fb-photo" role="img" aria-label="Photo of a bright living room with a wall-mounted air conditioner and a sofa"></div>
  <div class="abs fb-box"></div>
  <div class="abs fb-quote">&ldquo;</div>
  <p class="abs fb-text">Excellent service. Marcus came and quoted at the agreed time. The team showed up on time and completed on time. Marcus and his guys were friendly and professional and I would highly recommend them. I will look to them for any future work.</p>
  <div class="abs fb-name">Rohan P from Hoppers Crossing, VIC</div>
  <div class="abs fb-date">10 May 2019</div>
  <div class="btn fb-btn">Leave Feedback</div>

  <!-- call -->
  <div class="abs call"></div>
  <div class="abs heading call-label">Call us on :</div>
  <div class="abs call-icon"><span>
    <svg width="26" height="26" viewBox="0 0 24 24"><path d="M6.6 3.5c1-.7 1.8-.5 2.3.5l1 2.2c.4.8.2 1.4-.5 2-.6.5-.6.9-.2 1.6.9 1.5 2 2.6 3.4 3.4.7.4 1.1.4 1.6-.2.6-.7 1.2-.9 2-.5l2.2 1c1 .5 1.2 1.3.5 2.3-1.4 1.8-3.6 2-6.6.1-2.8-1.8-4.9-3.9-6.6-6.7-1.8-3-1.6-4.9.9-6.2z" fill="#fff"/></svg>
  </span></div>
  <div class="abs call-number">041 738 5926</div>
  <p class="abs call-text">We are committed to best practice electrical safety standards and highest quality performance on the job</p>

  <!-- footer -->
  <div class="abs brand" style="top:4084px">
    <div class="brand-mark"></div>
    <div>
      <div class="brand-name">TOLVAR</div>
      <div class="brand-sub">AIR AND ELECTRICAL</div>
    </div>
  </div>
  <div class="abs social"><span></span><span></span><span></span><span></span></div>

  <div class="abs foot-head" style="left:347px">Sitemap</div>
  <ul class="abs foot-list" style="left:347px">
    <li>Home</li><li>About</li><li>Why Us</li><li>Quality</li><li>Price</li><li>Services</li><li>Feedback</li><li>Contact Us</li>
  </ul>
  <div class="abs foot-head" style="left:612px">Services</div>
  <ul class="abs foot-list" style="left:612px">
    <li>Domestic</li><li>Commercial</li><li>Industrial</li><li>Split System Installations</li><li>Data &amp; Communication Installation</li><li>Electrical Testing &amp; Tagging</li><li>24hr Breakdown &amp; Repair Service</li>
  </ul>
  <div class="abs foot-head" style="left:879px">Contact Us</div>
  <ul class="abs foot-contact">
    <li style="top:0"><svg width="20" height="20" viewBox="0 0 24 24"><path d="M6.6 3.5c1-.7 1.8-.5 2.3.5l1 2.2c.4.8.2 1.4-.5 2-.6.5-.6.9-.2 1.6.9 1.5 2 2.6 3.4 3.4.7.4 1.1.4 1.6-.2.6-.7 1.2-.9 2-.5l2.2 1c1 .5 1.2 1.3.5 2.3-1.4 1.8-3.6 2-6.6.1-2.8-1.8-4.9-3.9-6.6-6.7-1.8-3-1.6-4.9.9-6.2z" fill="#ee1c25"/></svg>041 738 5926</li>
    <li style="top:35px"><svg width="20" height="16" viewBox="0 0 20 16"><rect width="20" height="16" rx="2" fill="#ee1c25"/><path d="M1 2l9 7 9-7" fill="none" stroke="#fff" stroke-width="1.6"/></svg>info@tolvar.com</li>
    <li style="top:76px"><svg width="20" height="20" viewBox="0 0 20 20"><circle cx="10" cy="10" r="9" fill="#ee1c25"/><path d="M1 10h18M10 1c-4 4-4 14 0 18M10 1c4 4 4 14 0 18" fill="none" stroke="#fff" stroke-width="1.2"/></svg>tolvar.com.au</li>
    <li style="top:112px"><svg width="20" height="20" viewBox="0 0 20 20"><circle cx="10" cy="10" r="9" fill="#ee1c25"/><path d="M1 10h18M10 1c-4 4-4 14 0 18M10 1c4 4 4 14 0 18" fill="none" stroke="#fff" stroke-width="1.2"/></svg>tolvarelectrical.com.au</li>
    <li style="top:149px"><svg width="20" height="20" viewBox="0 0 20 20"><circle cx="10" cy="10" r="9" fill="#ee1c25"/><path d="M1 10h18M10 1c-4 4-4 14 0 18M10 1c4 4 4 14 0 18" fill="none" stroke="#fff" stroke-width="1.2"/></svg>tolvarairandelectrical.com.au</li>
    <li style="top:185px"><svg width="20" height="20" viewBox="0 0 20 20"><circle cx="10" cy="10" r="9" fill="#ee1c25"/><path d="M1 10h18M10 1c-4 4-4 14 0 18M10 1c4 4 4 14 0 18" fill="none" stroke="#fff" stroke-width="1.2"/></svg>tolvarair.com.au</li>
  </ul>
  <div class="abs foot-rule"></div>
  <div class="abs copy">&copy;TOLVAR &nbsp;- 2019 All Rights Reserved.</div>
</div>
</body>
</html>
```